Quote Cards With KB May 2025 for Instagram

I would like to put these quotes over one of the pictures attached; Instagram (new size: 4:5 (1080 x 1350 pixels) One Quote per picture, and I want the quote to be bold or easy to read as well. I provided a few reference graphics that I really like as examples below. In very small letters at the bottom add @KBHarlowOnline

All of the pictures are attached; you can pick any photo and add one quote to it; but no stock photography

```html
<!DOCTYPE html>
<html lang="en">
<head>
<meta charset="utf-8">
<title>Quote Cards — KB Harlow</title>
<link href="https://fonts.googleapis.com/css2?family=Cinzel:wght@500;600&family=Quicksand:wght@600;700&display=swap" rel="stylesheet">
<style>
  :root {
    --page-bg: #e9e5e7;
    --pink-hot: #ea2a9c;
    --pink-deep: #d0137f;
    --pink-soft: #f25cae;
    --white: #ffffff;
    --photo-violet: #7a4fc9;
    --photo-rose: #b86a8f;
    --photo-grey: #d9d4d6;
  }
  * { margin: 0; padding: 0; box-sizing: border-box; }
  html, body { width: 1200px; height: 4164px; overflow: hidden; }
  body { background: var(--page-bg); position: relative; }

  .card {
    position: absolute; left: 100px; width: 1000px; height: 1250px;
    overflow: hidden;
    box-shadow: 0 10px 40px rgba(120, 40, 90, 0.12);
  }
  .card--hormones { top: 97px; }
  .card--flat-tummy { top: 1437px; }
  .card--bloating { top: 2795px; }

  .photo { position: absolute; }
  .teaser, .headline, .handle { position: absolute; color: var(--white); }
  .teaser {
    font-family: "Quicksand", sans-serif; font-weight: 700;
    font-size: 50px; line-height: 74px;
    text-shadow: 0 2px 6px rgba(90, 0, 50, 0.35);
  }
  .headline {
    font-family: "Cinzel", serif; font-weight: 600;
    font-size: 60px; line-height: 84px;
    white-space: nowrap;
    text-shadow: 0 2px 8px rgba(90, 0, 50, 0.35);
  }
  .handle {
    font-family: "Quicksand", sans-serif; font-weight: 700;
    font-size: 26px;
  }

  /* Card 1 */
  .card--hormones .photo {
    inset: 0;
    background: linear-gradient(115deg, var(--pink-hot) 0%, var(--photo-violet) 55%, #e2559d 80%, #f08a4b 100%);
  }
  .card--hormones .panel {
    position: absolute; left: 0; top: 0; width: 482px; height: 100%;
    background: linear-gradient(180deg, rgba(236, 40, 156, 0.92), rgba(224, 30, 150, 0.9));
  }
  .card--hormones .teaser { left: 50px; top: 88px; }
  .card--hormones .headline { left: 50px; top: 432px; }
  .card--hormones .handle { left: 50px; top: 1170px; }

  /* Card 2 */
  .card--flat-tummy .photo {
    left: 0; top: 0; width: 500px; height: 100%;
    background: linear-gradient(180deg, #b9c3cc 0%, var(--photo-rose) 45%, #c7a24a 100%);
  }
  .card--flat-tummy .panel {
    position: absolute; left: 500px; top: 0; width: 500px; height: 100%;
    background: linear-gradient(160deg, var(--pink-soft), var(--pink-hot));
  }
  .card--flat-tummy .teaser { left: 543px; top: 125px; }
  .card--flat-tummy .headline { left: 543px; top: 330px; }
  .card--flat-tummy .handle { left: 550px; top: 1166px; }

  /* Card 3 */
  .card--bloating .photo {
    inset: 0;
    background: linear-gradient(180deg, var(--photo-grey) 0%, #cfc6cb 40%, #d77fae 62%, var(--pink-deep) 85%, #c80f78 100%);
  }
  .card--bloating .frame { position: absolute; inset: 0; }
  .card--bloating .teaser,
  .card--bloating .headline { left: 0; width: 100%; text-align: center; }
  .card--bloating .teaser { top: 772px; font-size: 52px; }
  .card--bloating .headline { top: 940px; font-size: 56px; line-height: 74px; }
  .card--bloating .handle { left: 0; width: 100%; text-align: center; top: 1188px; }
</style>
</head>
<body>

<section class="card card--hormones">
  <div class="photo" role="img" aria-label="Photo of KB in a fuchsia gown on a stage with colourful light streaks"></div>
  <div class="panel"></div>
  <p class="teaser">The<br>stubborn<br>belly fat<br>after 40?</p>
  <h2 class="headline">IT'S NOT<br>ABOUT<br>CALORIES;<br>IT'S<br>ABOUT YOUR<br>HORMONES.<br>HERE IS<br>THE FIX!</h2>
  <p class="handle">@KBHarlowOnline</p>
</section>

<section class="card card--flat-tummy">
  <div class="photo" role="img" aria-label="Photo of KB in a pink embellished outfit in front of mirrors and sunflowers"></div>
  <div class="panel"></div>
  <p class="teaser">Flat tummy<br>in your 40s?</p>
  <h2 class="headline">IT'S STILL<br>POSSIBLE!<br>COMMENT<br>BYE BELLY TO<br>GET THE<br>10 SECRETS<br>TO A<br>FLATTER<br>TUMMY</h2>
  <p class="handle">@KBHarlowOnline</p>
</section>

<section class="card card--bloating">
  <div class="photo" role="img" aria-label="Photo of KB dancing in a kitchen wearing a white cropped sweater"></div>
  <svg class="frame" width="1000" height="1250" viewBox="0 0 1000 1250" aria-hidden="true">
    <path d="M50 165 V29 H205" fill="none" stroke="#ffffff" stroke-width="4"/>
    <path d="M971 1080 V1217 H815" fill="none" stroke="#ffffff" stroke-width="4"/>
  </svg>
  <p class="teaser">Bloating. Muffin top. Puffy<br>waistline.</p>
  <h2 class="headline">YOUR BODY'S<br>SCREAMING FOR A DIFFERENT<br>KIND OF FIX. HERE IT IS</h2>
  <p class="handle">@KBHarlowOnline</p>
</section>

</body>
</html>
```